Business Card For Halvenmoor Financial Consulting

Hi, I would like a business card designed. Bold, modern.
Please use the same design as the logo. I have also attached the website design to see the overall theme.
Wordmark Font
Color: Hex: #01AEF7

```html
<!DOCTYPE html>
<html lang="en">
<head>
<meta charset="utf-8">
<title>Halvenmoor Financial Consulting – Business Card</title>
<link href="https://fonts.googleapis.com/css2?family=Montserrat:wght@700&family=Open+Sans:wght@400;600;700&display=swap" rel="stylesheet">
<style>
  :root{
    --bg:#2a2b2e;
    --card:#0b4469;
    --card-edge:#083756;
    --accent:#2ea3e6;
    --brand:#01aef7;
    --white:#ffffff;
    --faint:rgba(255,255,255,0.07);
  }
  *{box-sizing:border-box;margin:0;padding:0}
  html,body{width:1200px;height:780px;overflow:hidden;background:var(--bg)}
  .canvas{position:relative;width:1200px;height:780px}
  .card{position:absolute;width:540px;height:309px;background:var(--card);
        border-bottom:3px solid var(--card-edge);overflow:hidden}
  .card--front{left:70px;top:90px}
  .card--back{left:590px;top:380px}

  .brand{display:flex;align-items:center;gap:14px}
  .brand__mark{width:30px;height:30px;border:4px solid var(--accent);flex:none}
  .brand__name{font-family:"Montserrat",sans-serif;font-weight:700;color:var(--white);
               text-transform:uppercase;letter-spacing:1px;line-height:1.1}
  .card--front .brand{position:absolute;left:0;right:0;top:0;bottom:0;justify-content:center}
  .card--front .brand__mark{width:46px;height:46px;border-width:5px}
  .card--front .brand__name{font-size:26px}

  .card--back .brand{position:absolute;left:28px;top:26px;gap:10px}
  .card--back .brand__mark{width:24px;height:24px;border-width:3px}
  .card--back .brand__name{font-size:15px}

  .backdrop{position:absolute;left:300px;top:20px;width:200px;height:200px;
            border:22px solid var(--faint)}

  .divider{position:absolute;height:1.5px;background:var(--white)}
  .divider--main{left:0;right:30px;top:170px}
  .divider--address{left:28px;width:200px;top:208px}

  .person{position:absolute;right:38px;top:120px;text-align:right}
  .person__name{font-family:"Open Sans",sans-serif;font-weight:700;font-size:22px;color:var(--accent)}
  .person__role{font-family:"Open Sans",sans-serif;font-weight:400;font-size:13px;color:var(--white);margin-top:2px}

  .address{position:absolute;left:28px;top:216px;font-family:"Open Sans",sans-serif;
           font-size:12px;line-height:1.4;color:var(--white)}
  .contacts{position:absolute;left:300px;top:214px;list-style:none;font-family:"Open Sans",sans-serif;
            font-size:12px;color:var(--white)}
  .contacts li{display:flex;align-items:center;gap:8px;line-height:1.6}
  .contacts svg{width:12px;height:12px;fill:var(--accent);flex:none}
</style>
</head>
<body>
<div class="canvas">

  <section class="card card--front" aria-label="Card front">
    <div class="brand">
      <span class="brand__mark"></span>
      <span class="brand__name">Halvenmoor<br>Financial Consulting</span>
    </div>
  </section>

  <section class="card card--back" aria-label="Card back">
    <div class="backdrop"></div>
    <div class="brand">
      <span class="brand__mark"></span>
      <span class="brand__name">Halvenmoor<br>Financial Consulting</span>
    </div>

    <div class="person">
      <p class="person__name">Marta Veselá</p>
      <p class="person__role">Managing Director</p>
    </div>
    <div class="divider divider--main"></div>

    <div class="divider divider--address"></div>
    <address class="address" style="font-style:normal">
      1840 Brookline Ave. Suite 300<br>
      Arden Falls, TX 75099
    </address>

    <ul class="contacts">
      <li>
        <svg viewBox="0 0 24 24" aria-hidden="true"><path d="M6.6 10.8a15.1 15.1 0 0 0 6.6 6.6l2.2-2.2a1 1 0 0 1 1-.25 11.4 11.4 0 0 0 3.6.57 1 1 0 0 1 1 1V20a1 1 0 0 1-1 1A17 17 0 0 1 3 4a1 1 0 0 1 1-1h3.5a1 1 0 0 1 1 1c0 1.25.2 2.45.57 3.6a1 1 0 0 1-.25 1z"/></svg>
        (555) 214-0386
      </li>
      <li>
        <svg viewBox="0 0 24 24" aria-hidden="true"><path d="M2 5h20v14H2zm2 2v.5l8 5 8-5V7l-8 5z"/></svg>
        info@website.com
      </li>
      <li>
        <svg viewBox="0 0 24 24" aria-hidden="true"><circle cx="12" cy="12" r="10"/></svg>
        www.website.com
      </li>
    </ul>
  </section>

</div>
</body>
</html>
```